RTavenor Business Cards & Letterhead

I have a logo but need a design for some new business cards. We are a Design-Build Firm that specializes in the design and construction of commercial projects.
the cards need to be professional. no cartoon stuff.
i would like to have the cards in AI format so I can update the card as needed. Logo is provided.
Our Address is: 4187 Marlowe Ct. Apex, North Carolina 27614

```html
<!DOCTYPE html>
<html lang="en">
<head>
<meta charset="utf-8">
<title>RTavenor Business Card</title>
<link rel="stylesheet" href="https://fonts.googleapis.com/css2?family=Open+Sans:wght@400;700;800&display=swap">
<style>
:root{
  --bg:#4a4a49;
  --ink:#161616;
  --paper:#ffffff;
  --brand-blue:#0a62a8;
  --edge-blue:#1760c4;
  --steel:#5b5b5b;
  --mark-grey:#6c6c6c;
  --text-light:#f2f2f2;
}
*{margin:0;padding:0;box-sizing:border-box}
html,body{width:1200px;height:801px;overflow:hidden}
body{
  background:var(--bg);
  font-family:"Open Sans",sans-serif;
  position:relative;
}
.card{
  position:absolute;
  width:520px;height:297px;
  border-radius:16px;
  overflow:hidden;
  border-bottom:3px solid var(--edge-blue);
  box-shadow:0 18px 30px rgba(0,0,0,.35);
}
.card--front{left:45px;top:252px;background:var(--paper)}
.card--back{left:635px;top:252px;background:var(--ink)}
.card__art{position:absolute;inset:0;width:100%;height:100%}
.wordmark{
  position:absolute;
  display:flex;align-items:center;gap:12px;
  font-weight:800;letter-spacing:1px;
  text-transform:uppercase;
}
.wordmark__dot{width:28px;height:28px;background:var(--brand-blue)}
.card--front .wordmark{left:36px;top:58px;font-size:36px;color:#2b2b2b}
.card--back .wordmark{left:70px;top:126px;font-size:46px;color:var(--mark-grey)}
.card--back .wordmark__dot{width:34px;height:34px}
.contact{
  position:absolute;right:20px;top:158px;
  text-align:right;color:var(--text-light);
}
.contact__name{color:var(--brand-blue);font-weight:800;font-size:15px;letter-spacing:.5px;text-transform:uppercase;line-height:19px}
.contact__role{font-size:12px;line-height:16px;margin-bottom:10px}
.contact__line{font-size:12.5px;line-height:20px;display:flex;justify-content:flex-end;align-items:center;gap:8px}
.contact__icon{width:11px;height:11px;fill:var(--brand-blue)}
.address{
  position:absolute;left:150px;bottom:8px;
  color:var(--text-light);font-size:12.5px;line-height:19px;
}
.pattern{position:absolute;inset:0}
</style>
</head>
<body>

<section class="card card--front" aria-label="Business card front">
  <svg class="card__art" viewBox="0 0 520 297" preserveAspectRatio="none" aria-hidden="true">
    <defs>
      <path id="dark-field" d="M524 22 C450 22 425 70 395 120 C365 210 290 236 -4 240 L-4 300 L524 300 Z"/>
    </defs>
    <use href="#dark-field" fill="#5b5b5b" transform="translate(-14 -10)"/>
    <use href="#dark-field" fill="#ffffff" transform="translate(-9 -6)"/>
    <use href="#dark-field" fill="#0a62a8" transform="translate(-5 -3)"/>
    <use href="#dark-field" fill="#161616"/>
  </svg>
  <div class="wordmark"><span class="wordmark__dot"></span><span>RTavenor</span></div>
  <div class="contact">
    <p class="contact__name">Owen Harlan</p>
    <p class="contact__role">Managing Director</p>
    <p class="contact__line">123 456 789
      <svg class="contact__icon" viewBox="0 0 12 12"><path d="M2 1l2.5 0 1 3-1.5 1a7 7 0 0 0 3 3l1-1.5 3 1V10a1 1 0 0 1-1 1A9 9 0 0 1 1 2a1 1 0 0 1 1-1z"/></svg></p>
    <p class="contact__line">info@yourgmail.com
      <svg class="contact__icon" viewBox="0 0 12 12"><path d="M1 3h10v6H1z M1 3l5 4 5-4" stroke="#161616" stroke-width=".8"/></svg></p>
    <p class="contact__line">www.yourwebsite.com
      <svg class="contact__icon" viewBox="0 0 12 12"><circle cx="6" cy="6" r="5"/></svg></p>
  </div>
  <p class="address">4187 Marlowe Ct. Apex,<br>North Carolina 27614</p>
</section>

<section class="card card--back" aria-label="Business card back">
  <div class="pattern" role="img" aria-label="Embossed repeating brand monogram pattern in dark tones"
       style="background:radial-gradient(ellipse at 30% 20%,#2e2e2e 0%,#1c1c1c 45%,transparent 75%),linear-gradient(135deg,#262626 0%,#151515 55%,#0b0b0b 100%)"></div>
  <div class="wordmark"><span class="wordmark__dot"></span><span>RTavenor</span></div>
</section>

</body>
</html>
```